Brook Refrigeration. Refrigeration and air conditioning specialists.

We need a website to promote our business. We would a modern simple design using the colours from our logo and black. We want it to be fun but proffesional.

Target Market(s)

Commercial

Number of Pages Required

4 page

Requirements
Must have
• Home Page, About Us, Services and Contact Us.
• 24/7 365 days service available.
• Brook Refrigeration's dedicated team specialises in commercial refrigeration and air conditioning equipment.
• Based in Joondalup, we cover Perth Metro and surrounding areas.
Nice to have
• KNOWLEDGE . EXPERIENCE . PASSION in bold.
• Our experienced and highly trained technicians provide extensive knowledge and exceptional skills for your commercial refrigeration and air conditioning requirements.
• Pictures of commercial refrigeration.
Should not have
• No mention of domestic services.

```html
<!DOCTYPE html>
<html lang="en">
<head>
<meta charset="utf-8">
<title>Brook Refrigeration</title>
<link rel="stylesheet" href="https://fonts.googleapis.com/css2?family=Lato:wght@400;700;900&display=swap">
<style>
:root{
  --purple:#2e1450;
  --green:#8fee4a;
  --green-dark:#7fd93c;
  --ink:#333333;
  --muted:#555555;
  --grey-band:#efefef;
  --white:#ffffff;
}
*{box-sizing:border-box;margin:0;padding:0}
html,body{width:1200px;height:3327px;overflow:hidden;background:var(--white)}
body{position:relative;font-family:'Lato',sans-serif;color:var(--ink)}
.abs{position:absolute}
.btn{position:absolute;display:flex;align-items:center;justify-content:center;background:var(--green);color:var(--purple);font-weight:700;font-size:16px;letter-spacing:.3px;text-transform:uppercase}

/* header */
.site-header{position:absolute;left:0;top:0;width:1200px;height:118px;background:var(--white)}
.brand{position:absolute;left:75px;top:36px;display:flex;align-items:center;gap:10px;font-weight:900;font-size:24px;color:var(--green);text-transform:uppercase;letter-spacing:.5px}
.brand .mark{width:18px;height:18px;border-radius:50%;background:var(--green)}
.follow{position:absolute;left:749px;top:22px;display:flex;align-items:center;gap:12px;font-size:14px;font-weight:700;color:var(--purple)}
.social{width:16px;height:16px;border-radius:50%;background:var(--purple)}
.phone{position:absolute;left:950px;top:18px;display:flex;align-items:center;gap:10px;font-size:22px;font-weight:700;color:var(--purple)}
.nav{position:absolute;top:66px;left:730px;display:flex;font-size:16px;font-weight:700;color:var(--purple)}
.nav a{display:block;height:38px;line-height:38px;padding:0 19px;text-decoration:none;color:inherit}
.nav a.active{background:var(--green)}

/* hero */
.hero{position:absolute;left:0;top:118px;width:1200px;height:559px;background:linear-gradient(180deg,#cfd2d3 0%,#a9adae 45%,#8b8f8f 100%)}
.hero-copy{position:absolute;left:0;width:1200px;text-align:center;color:var(--white)}
.hero .intro{top:156px;font-size:31px;font-weight:700}
.hero .headline{top:190px;font-size:40px;font-weight:900;line-height:44px;text-transform:uppercase}
.hero .tagline{top:282px;font-size:31px;font-weight:900;color:var(--green)}
.dots{position:absolute;top:518px;left:564px;display:flex;gap:10px}
.dots span{width:11px;height:11px;border-radius:50%;background:var(--white)}
.dots span.on{background:var(--green)}

/* welcome */
.welcome-title{top:763px;left:0;width:1200px;text-align:center;font-size:29px;font-weight:900;color:var(--purple);text-transform:uppercase}
.welcome-title em{font-style:normal;color:var(--green)}
.welcome-text{top:822px;left:75px;width:1050px;text-align:center;font-size:20px;line-height:34px;color:var(--muted)}

/* services band */
.band{position:absolute;left:0;top:1025px}
.photo{position:absolute}
.service-title{font-size:30px;font-weight:900;color:var(--purple);text-transform:uppercase}
.service-text{font-size:15px;line-height:24px;color:var(--muted);width:490px}

/* offer */
.offer-title{top:2040px;left:0;width:1200px;text-align:center;font-size:29px;font-weight:900;color:var(--purple);text-transform:uppercase}
.offer{position:absolute;top:2126px;width:330px;text-align:center}
.offer .icon{width:104px;height:104px;margin:0 auto;border-radius:50%;background:var(--green);display:flex;align-items:center;justify-content:center}
.offer h3{margin-top:30px;font-size:19px;font-weight:900;line-height:25px;color:var(--ink);text-transform:uppercase}
.offer p{margin-top:6px;font-size:15px;line-height:23px;color:var(--muted)}

/* contact */
.contact-band{position:absolute;left:0;top:2457px}
.contact-title{top:2567px;left:0;width:1200px;text-align:center;font-size:29px;font-weight:900;color:var(--white);text-transform:uppercase}
.field{position:absolute;background:var(--white);font-size:15px;color:var(--muted);padding:0 16px;display:flex;align-items:center}
.field.area{align-items:flex-start;padding-top:18px}

/* footer */
.footer-brand{left:75px;top:3140px;display:flex;align-items:center;gap:10px;font-weight:900;font-size:24px;color:var(--green);text-transform:uppercase}
.footer-brand .mark{width:18px;height:18px;border-radius:50%;background:var(--green)}
.legal{left:75px;top:3218px;font-size:13px;line-height:24px;color:var(--muted)}
.fcol h4{font-size:15px;font-weight:900;color:var(--purple);text-transform:uppercase;margin-bottom:14px}
.fcol li{list-style:none;font-size:14px;line-height:33px;color:var(--purple)}
.fcol .row{display:flex;align-items:center;gap:16px;font-size:14px;line-height:28px;color:var(--purple)}
</style>
</head>
<body>

<header class="site-header">
  <div class="brand"><span class="mark"></span>Brook Refrigeration</div>
  <div class="follow">FOLLOW US <span class="social"></span><span class="social"></span></div>
  <div class="phone">
    <svg width="18" height="18" viewBox="0 0 24 24"><path fill="#2e1450" d="M6.6 10.8a15.1 15.1 0 0 0 6.6 6.6l2.2-2.2c.3-.3.7-.4 1-.2 1.1.4 2.3.6 3.6.6.6 0 1 .4 1 1V20c0 .6-.4 1-1 1A17 17 0 0 1 3 4c0-.6.4-1 1-1h3.5c.6 0 1 .4 1 1 0 1.3.2 2.5.6 3.6.1.3 0 .7-.2 1z"/></svg>
    1300-555-018
  </div>
  <nav class="nav"><a class="active">HOME</a><a>ABOUT</a><a>SERVICES</a><a>CONTACT</a></nav>
</header>

<section class="hero" role="img" aria-label="Photo of an empty commercial cool room with steel shelving and ceiling evaporator">
  <div class="hero-copy intro">Our dedicated team specialises in</div>
  <div class="hero-copy headline">Commercial Refrigeration &amp;<br>Air Conditioning Equipment</div>
  <div class="hero-copy tagline">KNOWLEDGE . EXPERIENCE . PASSION</div>
  <div class="btn" style="left:523px;top:346px;width:151px;height:44px">Read More</div>
  <div class="dots"><span class="on"></span><span></span><span></span><span></span></div>
</section>

<h1 class="abs welcome-title">Welcome to <em>Brook</em> Refrigeration</h1>
<p class="abs welcome-text">Brook Refrigeration are commercial refrigeration and air conditioning specialists providing a comprehensive service throughout the Perth Metro area - 24 hours / 7 days a week</p>
<div class="btn" style="left:523px;top:936px;width:151px;height:43px">Read More</div>

<svg class="band" width="1200" height="953" viewBox="0 0 1200 953"><polygon points="0,66 1200,0 1200,883 0,953" fill="#efefef"/></svg>

<div class="photo" style="left:75px;top:1151px;width:522px;height:351px;background:linear-gradient(135deg,#e4e6e7,#a7abad 60%,#6f7476)" role="img" aria-label="Photo of a row of stainless steel commercial upright fridges"></div>
<h2 class="abs service-title" style="left:621px;top:1186px">Commercial Refrigeration</h2>
<p class="abs service-text" style="left:621px;top:1242px">Lorem ipsum dolor sit amet, consectetur adipiscing elit. In ut leo sit amet mauris pellentesque lobortis. Praesent vulputate dictum venenatis. Pellentesque habitant morbi tristique senectus et netus et malesuada fames ac turpis egestas. Quisque sodales, dolor non convallis condimentum, arcu diam feugiat ligula...</p>
<div class="btn" style="left:621px;top:1397px;width:150px;height:45px">Read More</div>

<h2 class="abs service-title" style="left:75px;top:1547px">Air Conditioning Equipment</h2>
<p class="abs service-text" style="left:75px;top:1603px">Lorem ipsum dolor sit amet, consectetur adipiscing elit. In ut leo sit amet mauris pellentesque lobortis. Praesent vulputate dictum venenatis. Pellentesque habitant morbi tristique senectus et netus et malesuada fames ac turpis egestas. Quisque sodales, dolor non convallis condimentum, arcu diam feugiat ligula...</p>
<div class="btn" style="left:75px;top:1761px;width:151px;height:42px">Read More</div>
<div class="photo" style="left:603px;top:1502px;width:522px;height:350px;background:linear-gradient(160deg,#d8dcdd,#8e9598 55%,#3f4749)" role="img" aria-label="Photo of rooftop air conditioning condenser units"></div>

<h2 class="abs offer-title">What We Offer</h2>
<div class="offer" style="left:75px">
  <div class="icon"><svg width="52" height="52" viewBox="0 0 24 24"><circle cx="12" cy="12" r="9" fill="none" stroke="#2e1450" stroke-width="2.4"/><path d="M12 7v5h4" fill="none" stroke="#2e1450" stroke-width="2.4" stroke-linecap="round"/></svg></div>
  <h3>24/7 365 Days Service<br>Available</h3>
  <p>Lorem ipsum dolor sit amet, consectetur adipiscing elit. In ut leo sit amet mauris pellentesque lobortis</p>
</div>
<div class="offer" style="left:434px">
  <div class="icon"><svg width="52" height="52" viewBox="0 0 24 24"><path d="M7 9a5 5 0 0 1 10 0z" fill="#2e1450"/><rect x="6" y="9" width="12" height="1.6" fill="#2e1450"/><path d="M4 22c0-5 3.5-8 8-8s8 3 8 8z" fill="#2e1450"/></svg></div>
  <h3>Experienced &amp; Highly Trained<br>Technicians</h3>
  <p>Lorem ipsum dolor sit amet, consectetur adipiscing elit. In ut leo sit amet mauris pellentesque lobortis</p>
</div>
<div class="offer" style="left:795px">
  <div class="icon"><svg width="46" height="46" viewBox="0 0 24 24"><path d="M12 2a7 7 0 0 0-7 7c0 5 7 13 7 13s7-8 7-13a7 7 0 0 0-7-7z" fill="#2e1450"/><circle cx="12" cy="9" r="2.6" fill="#8fee4a"/></svg></div>
  <h3>Service Based in<br>Joondalup</h3>
  <p>Lorem ipsum dolor sit amet, consectetur adipiscing elit. In ut leo sit amet mauris pellentesque lobortis</p>
</div>

<svg class="contact-band" width="1200" height="640" viewBox="0 0 1200 640" role="img" aria-label="Dimmed photo of a supermarket aisle lined with refrigerated display cases">
  <defs><linearGradient id="contactShade" x1="0" y1="0" x2="0" y2="1"><stop offset="0" stop-color="#4a5052"/><stop offset=".5" stop-color="#6d7475"/><stop offset="1" stop-color="#3e4446"/></linearGradient></defs>
  <polygon points="0,71 1200,0 1200,582 0,637" fill="url(#contactShade)"/>
</svg>
<h2 class="abs contact-title">Quick Contact</h2>
<div class="field" style="left:226px;top:2644px;width:362px;height:51px">Name</div>
<div class="field" style="left:614px;top:2644px;width:360px;height:51px">Phone Name</div>
<div class="field" style="left:226px;top:2710px;width:362px;height:51px">Email Address</div>
<div class="field" style="left:614px;top:2710px;width:360px;height:51px">Company Name</div>
<div class="field area" style="left:226px;top:2777px;width:748px;height:133px">Message</div>
<div class="btn" style="left:523px;top:2945px;width:151px;height:43px">Submit</div>

<footer>
  <div class="abs footer-brand"><span class="mark"></span>Brook Refrigeration</div>
  <p class="abs legal">Copyright © 2018 Brook Refrigeration Pty Ltd.<br>All Rights Reserved.<br>ABN 00 000 000 000.</p>
  <div class="abs fcol" style="left:415px;top:3125px">
    <h4>Site Map</h4>
    <ul><li>Home</li><li>About</li><li>Services</li><li>Contact Us</li></ul>
  </div>
  <div class="abs fcol" style="left:628px;top:3125px">
    <h4>Contact Us</h4>
    <div style="font-size:14px;line-height:22px;color:var(--purple);margin-bottom:4px">12 Harbour Lane<br>Joondalup WA 6027</div>
    <div class="row"><svg width="12" height="12" viewBox="0 0 24 24"><path fill="#2e1450" d="M6.6 10.8a15.1 15.1 0 0 0 6.6 6.6l2.2-2.2c.3-.3.7-.4 1-.2 1.1.4 2.3.6 3.6.6.6 0 1 .4 1 1V20c0 .6-.4 1-1 1A17 17 0 0 1 3 4c0-.6.4-1 1-1h3.5c.6 0 1 .4 1 1 0 1.3.2 2.5.6 3.6.1.3 0 .7-.2 1z"/></svg>1-800-555-0142</div>
    <div class="row"><svg width="12" height="12" viewBox="0 0 24 24"><rect x="2" y="5" width="20" height="14" fill="#2e1450"/><path d="M2 5l10 8 10-8" fill="none" stroke="#fff" stroke-width="1.6"/></svg>hello@brookrefrigeration.example</div>
    <div class="row"><svg width="12" height="12" viewBox="0 0 24 24"><path d="M12 2a7 7 0 0 0-7 7c0 5 7 13 7 13s7-8 7-13a7 7 0 0 0-7-7z" fill="#2e1450"/></svg>Map Direction</div>
  </div>
  <div class="abs fcol" style="left:907px;top:3125px">
    <h4>Follow Us</h4>
    <div style="display:flex;gap:14px;margin-top:18px"><span class="social"></span><span class="social"></span></div>
  </div>
</footer>

</body>
</html>
```